Marrowby Water Taxi and Transport Business Card

I need business cards for my new water taxi and freight transport business I have started here in Kodiak Alaska. Kodiak is a remote island in the middle of the gulf of Alaska. There are seven native villages around the island and Kodiak is the #2 fishing port in the United States. We also have the largest Coast Guard Base in the U.S. My company will be providing water taxi and freight transport logistics to the villages and many hunting and fishing lodges as well as remote properties around the island.

I would like a business card that isn't status quo, something that stands out, either in feel or appearance. I do like clean minimal designs but it needs to have the necessary contact info on it.

Target Market(s)

remote lodge / property owners, residents of the many villages around Kodiak and any one wanting to enjoy the great outdoors of Kodiak Alaska

Industry/Entity Type

Business

Contact Information for Business Card

I like clean simple designs that aren't cluttered but still provide the necessary information

Colors
0255a3
3277b5
33a4d5
9bcb3c
add136
fbed22
ffc214
f78f20
f37122

Requirements
Must have
• logo and contact info
• Captain Mason Elwick
• www.marrowbyferryline.com
• mason@marrowbyferryline.com

```html
<!DOCTYPE html>
<html lang="en">
<head>
<meta charset="utf-8">
<title>Marrowby Water Taxi and Transport – Business Card</title>
<link rel="stylesheet" href="https://fonts.googleapis.com/css2?family=Exo+2:wght@700&family=Questrial&display=swap">
<style>
  :root {
    --stage: #e6e7e9;
    --card: #ffffff;
    --navy: #0255a3;
    --mid-blue: #3277b5;
    --sky: #33a4d5;
    --sun: #f78f20;
    --ink-white: #ffffff;
    --rule-grey: #9a9a9a;
  }
  * { box-sizing: border-box; margin: 0; padding: 0; }
  html, body {
    width: 1105px;
    height: 1200px;
    overflow: hidden;
    background: var(--stage);
  }
  .card {
    position: absolute;
    left: 196px;
    width: 720px;
    height: 412px;
    background: var(--card);
    overflow: hidden;
  }
  .card--front { top: 146px; }
  .card--back { top: 602px; }

  /* Front */
  .mountain-scene {
    position: absolute;
    left: 0;
    top: 44px;
    width: 100%;
    height: 368px;
    background: linear-gradient(180deg, var(--sky) 0%, var(--mid-blue) 35%, var(--navy) 70%);
  }
  .sun {
    position: absolute;
    right: 160px;
    top: 18px;
    width: 160px;
    height: 90px;
    background: var(--sun);
    border-radius: 80px 80px 0 0;
  }
  .front-details {
    position: absolute;
    left: 0;
    right: 0;
    top: 238px;
    text-align: center;
    color: var(--ink-white);
    font-family: "Questrial", sans-serif;
  }
  .person-name {
    font-family: "Exo 2", sans-serif;
    font-weight: 700;
    font-size: 25px;
    letter-spacing: 0.5px;
    text-transform: uppercase;
    line-height: 1;
  }
  .person-role {
    display: flex;
    align-items: center;
    justify-content: center;
    gap: 8px;
    font-size: 19px;
    margin-top: 4px;
  }
  .person-role::before,
  .person-role::after {
    content: "";
    width: 78px;
    height: 1px;
    background: var(--ink-white);
  }
  .contact-list {
    list-style: none;
    margin-top: 14px;
    font-size: 18px;
    line-height: 24px;
  }

  /* Back */
  .brand {
    position: absolute;
    left: 0;
    right: 0;
    top: 100px;
    display: flex;
    flex-direction: column;
    align-items: center;
    gap: 14px;
  }
  .brand-dot {
    width: 40px;
    height: 40px;
    border-radius: 50%;
    background: var(--sun);
  }
  .brand-name {
    font-family: "Questrial", sans-serif;
    font-size: 30px;
    line-height: 38px;
    color: var(--navy);
    text-align: center;
  }
  .social-row {
    position: absolute;
    left: 0;
    right: 0;
    top: 340px;
    display: flex;
    align-items: center;
    justify-content: center;
    gap: 4px;
  }
  .social-row .rule {
    width: 86px;
    height: 1px;
    background: linear-gradient(90deg, transparent, var(--rule-grey), transparent);
    margin: 0 10px;
  }
  .social-dot {
    width: 30px;
    height: 30px;
    border-radius: 50%;
  }
  .social-dot--one { background: var(--mid-blue); }
  .social-dot--two { background: var(--sky); }
  .social-dot--three { background: var(--navy); }
</style>
</head>
<body>
  <section class="card card--front">
    <div class="mountain-scene" role="img" aria-label="Illustration of blue mountain peaks with an orange sun behind them"></div>
    <div class="sun" role="img" aria-label="Orange sun rising behind the peaks"></div>
    <div class="front-details">
      <h1 class="person-name">Mason Elwick</h1>
      <p class="person-role">Captain</p>
      <ul class="contact-list">
        <li>412 Harbor Bluff Road, Kodiak, Alaska 99615</li>
        <li>555 218 4760 | mason@marrowbyferryline.com</li>
        <li>www.marrowbyferryline.com</li>
      </ul>
    </div>
  </section>

  <section class="card card--back">
    <div class="brand">
      <span class="brand-dot"></span>
      <p class="brand-name">Marrowby<br>Water Taxi and Transport</p>
    </div>
    <div class="social-row">
      <span class="rule"></span>
      <span class="social-dot social-dot--one"></span>
      <span class="social-dot social-dot--two"></span>
      <span class="social-dot social-dot--three"></span>
      <span class="rule"></span>
    </div>
  </section>
</body>
</html>
```